Home page design for Drone video business (the Business focusses on home videos for realtors)

Dear reader,

*I NEED DESIGNS OF ALL THE PAGES*
We need a first design of a homepage and of 4 other pages of the website of a business that sells drone video services. All the pages will need to be in the similar design style.
The video's are targeted at consumers that want to sell there home and would like to have a cool drone video of photos of their home.

How does the website look:
- has a navbar on top
- A cool looking banner of an areal drone.
- A Big header: with company name: SkyLoftReels
- A smaller subheader: We film your home to increase your chances of sale
- Then a section with a Big header: How does it work
- In this section a place for a vimeo explainitory video
- Then a similar navbar styled bar with a phone number and a email address
- Then a section where the videos porfolio is displayed in a cool way
- Inside this sectiona header: Our work

- A section with header: Why us?
- 4 symbols here with a subheader and some lorum ipsum text underneath (see wireframe images)

- Under that a: Contact us
- where you can put in name, email, phone, message box and a send button

- At the bottom a footer with phone number and a fake address for now.

Be creative. Use creative but serious color.
Use a serious font. Make it a sharp design. Sharp lines. Not to dark design and not to light design.

The wireframes are the same kind of images.
PLEASE PUT IN DESIGNS OF ALL THE PAGES

Good luck

Target Market(s)

People that want to sell home and want to make a cool drone video or photos of their home.

Industry/Entity Type

Business

Contact Information for Business Card

Lucas Wenning
lucas@skyloftreels.example
+31647208351

Logo Text

SkyLoftReels

Number of Pages Required

1 page

Font styles to use
Sans Serif

Requirements
Must have
• All the sections as explained in the instructions.
• The nav bar should have an about us, services, portfolio and a contact us buttons.
• See instruction for details.
• Must include designs of the front page, contact us, our services, portfolio and contact us.
• If you do add some designs for the "about us", "services", "prices", "portfolio" and "contact us" pages, you make a way better chance of winning the competition.
Nice to have
• designs for the other pages as described at the Must haves. You make a better chance of winning if you include them. Look at the wireframes to see the mockups for those pages. think creative about what kind of sections and design should be included in those pages.
Should not have
• bad designs.

```html
<!DOCTYPE html>
<html lang="en">
<head>
<meta charset="utf-8">
<title>SkyLoftReels – About Us</title>
<link href="https://fonts.googleapis.com/css2?family=Open+Sans:wght@400;600;700&family=Montserrat:wght@700;800&family=PT+Sans+Narrow&display=swap" rel="stylesheet">
<style>
:root{
  --green:#7ab322;
  --green-dark:#5f8f17;
  --slate:#4a525a;
  --slate-dark:#394047;
  --slate-bar:#454c53;
  --nav:#3f464d;
  --white:#ffffff;
  --muted:#e8ecef;
}
*{margin:0;padding:0;box-sizing:border-box}
html,body{width:775px;height:1200px;overflow:hidden;background:var(--slate)}
body{position:relative;font-family:"Open Sans",sans-serif;color:var(--white)}
.abs{position:absolute}

/* nav */
.topnav{left:0;top:0;width:775px;height:46px;background:var(--nav);border-bottom:3px solid var(--green)}
.brand{left:106px;top:0;width:102px;height:58px;background:#f3f5f2;border-radius:0 0 6px 6px;box-shadow:0 2px 4px rgba(0,0,0,.3);display:flex;align-items:center;justify-content:center;z-index:3}
.brand span{font-family:"Open Sans",sans-serif;font-weight:700;font-size:12.5px;color:var(--green-dark)}
.menu{left:300px;top:12px;display:flex;gap:6px;z-index:3}
.menu a{font-size:11.5px;font-weight:700;letter-spacing:.8px;color:var(--white);text-decoration:none;padding:4px 8px;border-radius:14px}
.menu a.active{background:var(--white);color:var(--green)}

/* hero */
.hero{left:0;top:49px;width:775px;height:351px;background:radial-gradient(ellipse at 60% 40%,#5c6a5c 0%,#485448 45%,#3b463c 100%);border-bottom:2px solid #2e3338}
.team-photo{left:34px;top:100px;width:321px;height:254px;background:linear-gradient(180deg,#e9eef3 0%,#cfd8e2 55%,#8e9aa7 100%)}
.hero-title{left:372px;top:108px;width:375px;text-align:center;font-family:"Montserrat",sans-serif;font-weight:800;font-size:38px;letter-spacing:1px;color:var(--green)}
.hero-text{left:366px;top:172px;width:385px;text-align:center;font-family:"PT Sans Narrow",sans-serif;font-size:24px;line-height:23.3px;color:var(--white)}

/* how we work */
.section-title{left:0;top:450px;width:775px;text-align:center;font-size:20px;font-weight:600;letter-spacing:1px}
.title-rule{left:350px;top:483px;width:75px;height:3px;background:var(--green)}
.section-intro{left:0;top:503px;width:775px;text-align:center;font-size:9.6px;font-weight:700;line-height:12px;letter-spacing:.3px}
.step{left:134px;width:520px;height:42px}
.step-num{position:absolute;left:0;top:0;width:42px;height:42px;border:2px solid var(--green);border-radius:50%;display:flex;align-items:center;justify-content:center;font-size:22px;font-weight:400}
.step-text{position:absolute;left:59px;top:3px;font-size:10.4px;font-weight:600;line-height:13.2px;letter-spacing:.3px;white-space:nowrap}

/* contact band */
.contact-band{left:0;top:918px;width:775px;height:64px;background:var(--green)}
.band-item{top:924px;display:flex;align-items:center;gap:8px;font-family:"Montserrat",sans-serif;font-weight:700;font-size:23px;color:var(--white)}
.band-icon{width:48px;height:48px}

/* footer */
.footer{left:0;top:982px;width:775px;height:180px;background:var(--slate-dark)}
.foot-head{font-size:15px;font-weight:600;letter-spacing:.8px}
.foot-rule{height:3px;width:76px;background:var(--green)}
.foot-about{left:90px;top:1050px;font-size:12.2px;font-weight:600;line-height:20px;letter-spacing:.2px}
.foot-links{left:314px;top:1053px;list-style:none}
.foot-links li{font-size:10.4px;font-weight:700;letter-spacing:.8px;height:19.6px;display:flex;align-items:center;gap:11px}
.foot-links li b{color:var(--green);font-size:12px}
.news-input{left:512px;top:1056px;width:164px;height:30px;background:var(--white);border:1px solid #ccc;font-size:9.5px;color:#9aa0a6;padding:9px 14px}
.news-btn{left:512px;top:1098px;width:104px;height:28px;background:var(--green);display:flex;align-items:center;justify-content:center;font-size:12.5px;font-weight:700;letter-spacing:1px}

/* bottom bar */
.bottom-bar{left:0;top:1162px;width:775px;height:38px;background:var(--slate-bar);border-top:2px solid #2f353a}
.copyright{left:90px;top:1173px;font-size:12.5px;font-weight:700;letter-spacing:.3px}
.socials{left:543px;top:1168px;display:flex;gap:3px}
.socials span{width:26px;height:26px;background:#2c3136}
.to-top{left:738px;top:1143px;width:31px;height:31px;background:var(--green);display:flex;align-items:center;justify-content:center}
</style>
</head>
<body>

<div class="abs hero"></div>
<div class="abs team-photo" role="img" aria-label="Team portrait of four professionals in business attire"></div>
<h1 class="abs hero-title">OUR TEAM</h1>
<p class="abs hero-text">Lorem ipsum dolor sit amet consectetuer adipiscing elit Suspendisse et justo.Lorem ipsum dolor sit amet elit et justoLorem ipsum dolor sit amet consectetuer eet justo. justoLorem ipsum dolor sit amet consectetuer eet justo.</p>

<header class="abs topnav"></header>
<div class="abs brand"><span>SkyLoftReels</span></div>
<nav class="abs menu">
  <a href="#">HOME</a><a href="#">SERVICES</a><a href="#" class="active">ABOUT US</a><a href="#">PORTFOLIO</a><a href="#">CONTACT</a>
</nav>

<h2 class="abs section-title">HOW WE WORK</h2>
<div class="abs title-rule"></div>
<p class="abs section-intro">Lorem ipsum dolor sit amet consectetuer<br>adipiscing elit. Suspendisse et justo.</p>

<div class="abs step" style="top:565px"><div class="step-num">I</div><p class="step-text">Lorem ipsum dolor sit amet consectetuer adipiscing elit. Suspendisse et justo.<br>Lorem ipsum dolor sit amet consectetuer adipiscing elit. Suspendisse et justo<br>Lorem ipsum dolor sit amet consectetuer adipiscing elit. Suspendisse et justo.</p></div>
<div class="abs step" style="top:641px"><div class="step-num">II</div><p class="step-text">Lorem ipsum dolor sit amet consectetuer adipiscing elit. Suspendisse et justo.<br>Lorem ipsum dolor sit amet consectetuer adipiscing elit. Suspendisse et justo<br>Lorem ipsum dolor sit amet consectetuer adipiscing elit. Suspendisse et justo.</p></div>
<div class="abs step" style="top:717px"><div class="step-num">III</div><p class="step-text">Lorem ipsum dolor sit amet consectetuer adipiscing elit. Suspendisse et justo.<br>Lorem ipsum dolor sit amet consectetuer adipiscing elit. Suspendisse et justo<br>Lorem ipsum dolor sit amet consectetuer adipiscing elit. Suspendisse et justo.</p></div>
<div class="abs step" style="top:796px"><div class="step-num">IV</div><p class="step-text">Lorem ipsum dolor sit amet consectetuer adipiscing elit. Suspendisse et justo.<br>Lorem ipsum dolor sit amet consectetuer adipiscing elit. Suspendisse et justo<br>Lorem ipsum dolor sit amet consectetuer adipiscing elit. Suspendisse et justo.</p></div>

<div class="abs contact-band"></div>
<div class="abs band-item" style="left:87px">
  <svg class="band-icon" viewBox="0 0 48 48"><circle cx="24" cy="24" r="22" fill="none" stroke="#fff" stroke-width="2.5"/><path d="M16 13c2-1 3 0 4 2l2 4c1 2 0 3-1 4l-1 1c1 3 3 5 6 6l1-1c1-1 2-2 4-1l4 2c2 1 3 2 2 4-1 3-4 4-7 3-7-2-13-8-15-15-1-3 0-7 1-9z" fill="#fff"/></svg>
  <span>+31647208351</span>
</div>
<div class="abs band-item" style="left:397px;font-size:19px">
  <svg class="band-icon" viewBox="0 0 48 48"><circle cx="24" cy="24" r="22" fill="none" stroke="#fff" stroke-width="2.5"/><rect x="12" y="16" width="24" height="16" fill="none" stroke="#fff" stroke-width="2"/><path d="M12 16l12 10 12-10M12 32l9-8M36 32l-9-8" fill="none" stroke="#fff" stroke-width="2"/></svg>
  <span>contact@skyloftreels.example</span>
</div>

<footer class="abs footer"></footer>
<h3 class="abs foot-head" style="left:90px;top:1004px">ABOUT US</h3>
<div class="abs foot-rule" style="left:90px;top:1033px"></div>
<p class="abs foot-about">Lorem ipsum dolor sit<br>consectetuer adipiscing.<br>Suspendisse et justo.<br>Suspendisse et justo.</p>

<h3 class="abs foot-head" style="left:314px;top:1006px">USEFULL LINKS</h3>
<div class="abs foot-rule" style="left:314px;top:1035px"></div>
<ul class="abs foot-links">
  <li><b>&gt;</b>HOME</li><li><b>&gt;</b>PORTFOLIO</li><li><b>&gt;</b>CONTACT US</li><li><b>&gt;</b>SERVICES</li>
</ul>

<h3 class="abs foot-head" style="left:511px;top:1009px">NEWSLETTER</h3>
<div class="abs foot-rule" style="left:513px;top:1035px"></div>
<div class="abs news-input">Your email Address...</div>
<div class="abs news-btn">SUBCRIBE</div>

<div class="abs bottom-bar"></div>
<p class="abs copyright">© SkyLoftReels 2016.</p>
<div class="abs socials"><span></span><span></span><span></span><span></span><span></span></div>
<div class="abs to-top"><svg width="10" height="8" viewBox="0 0 10 8"><path d="M1 6l4-4 4 4" fill="none" stroke="#fff" stroke-width="2"/></svg></div>

</body>
</html>
```